LLC needs a business card design that emphasizes consulting and expert witness in upstream oil and g

I need a business card design for my company called Obena Consultative Service, LLC. My expertise is in oil and gas upstream operations management to optimize performance and also as an expert witness for law firms in oil and gas upstream operations litigation.
The final design should communicate knowledge and hands-on experience as well as trust. (Obena means rope or lasso. Perhaps "Obena" should be in the form of a rope.) I do not like the color green in any shade. My first preference would be some shade of blue.
Industry/Entity Type
Oil And Gas

```html
<!DOCTYPE html>
<html lang="en">
<head>
<meta charset="utf-8">
<title>Obena Consultative Service, LLC — Business Card</title>
<link rel="stylesheet" href="https://fonts.googleapis.com/css2?family=Tinos:wght@400&display=swap">
<style>
  :root {
    --navy: #1d3a72;
    --band-top: #4a7cc6;
    --band-bottom: #24509a;
    --gold: #f0a81c;
    --ink: #1a2c55;
    --card: #ffffff;
    --stage: #e9e9ec;
    --ghost: #eeeff3;
    --icon-bg: #111111;
  }
  * { margin: 0; padding: 0; box-sizing: border-box; }
  html, body { width: 1200px; height: 892px; overflow: hidden; }
  body { background: var(--stage); position: relative; font-family: "Tinos", "Times New Roman", serif; }

  .card {
    position: absolute;
    width: 540px; height: 309px;
    background: var(--card);
    box-shadow: 0 6px 18px rgba(0,0,0,.15);
    overflow: hidden;
  }
  .card--front { left: 40px; top: 291px; }
  .card--back { left: 620px; top: 291px; }

  .wordmark {
    position: absolute;
    font-family: "Tinos", "Times New Roman", serif;
    font-weight: 400;
    color: var(--navy);
    white-space: nowrap;
    line-height: 1;
  }
  .card--front .wordmark { left: 34px; top: 40px; font-size: 28px; }
  .card--back .wordmark { left: 0; right: 0; top: 137px; text-align: center; font-size: 32px; }

  .person { position: absolute; left: 34px; top: 104px; color: var(--gold); }
  .person__name { font-size: 20px; line-height: 1.1; }
  .person__role { font-size: 13px; }

  .contacts { position: absolute; left: 34px; top: 162px; list-style: none; }
  .contacts li { display: flex; align-items: center; gap: 8px; height: 19px; color: var(--ink); font-size: 14px; }
  .contacts .icon {
    width: 16px; height: 16px; border-radius: 3px; background: var(--icon-bg);
    display: flex; align-items: center; justify-content: center; flex: none;
  }

  .band {
    position: absolute; left: 0; right: 0; bottom: 0; height: 52px;
    background: linear-gradient(to bottom, var(--band-top), var(--band-bottom));
  }
  .ghost-word {
    position: absolute; left: 340px; top: 119px;
    width: 260px; height: 72px; line-height: 72px;
    text-align: center; white-space: nowrap;
    font-family: "Tinos", "Times New Roman", serif; font-size: 64px; color: var(--ghost);
    transform: rotate(-90deg); transform-origin: center; letter-spacing: 2px;
  }
</style>
</head>
<body>
  <section class="card card--front" aria-label="Card front">
    <div class="ghost-word" aria-hidden="true">OBENA</div>
    <div class="wordmark">Obena Consultative Service, LLC</div>
    <div class="person">
      <div class="person__name">Employee Name</div>
      <div class="person__role">Your Position</div>
    </div>
    <ul class="contacts">
      <li><span class="icon"><svg width="11" height="11" viewBox="0 0 24 24"><path fill="#f0a81c" d="M6.6 10.8a15 15 0 0 0 6.6 6.6l2.2-2.2c.3-.3.7-.4 1-.2 1.1.4 2.3.6 3.6.6.6 0 1 .4 1 1V20c0 .6-.4 1-1 1A17 17 0 0 1 3 4c0-.6.4-1 1-1h3.5c.6 0 1 .4 1 1 0 1.3.2 2.5.6 3.6.1.3 0 .7-.2 1z"/></svg></span>550-00000-00</li>
      <li><span class="icon"><svg width="11" height="11" viewBox="0 0 24 24" fill="none" stroke="#f0a81c" stroke-width="2"><circle cx="12" cy="12" r="9"/><path d="M3 12h18M12 3c3 3 3 15 0 18M12 3c-3 3-3 15 0 18"/></svg></span>www.obenaconsultative.com</li>
      <li><span class="icon"><svg width="11" height="11" viewBox="0 0 24 24" fill="none" stroke="#f0a81c" stroke-width="2"><rect x="3" y="6" width="18" height="12"/><path d="M3 6l9 7 9-7"/></svg></span>obenaconsultative@mailbox.com</li>
      <li><span class="icon"><svg width="11" height="11" viewBox="0 0 24 24"><path fill="#f0a81c" d="M12 2a7 7 0 0 0-7 7c0 5 7 13 7 13s7-8 7-13a7 7 0 0 0-7-7zm0 9.5A2.5 2.5 0 1 1 12 6.5a2.5 2.5 0 0 1 0 5z"/></svg></span>0000 Harbor Lane, NY 00000</li>
    </ul>
    <div class="band"></div>
  </section>

  <section class="card card--back" aria-label="Card back">
    <div class="wordmark">Obena Consultative Service, LLC</div>
  </section>
</body>
</html>
```